Aerial Imaging and photgraphy business card

Design a business card with eye catching aerial photo of country side / landscape with a drone in the foreground.
Also contact details.

Target Market(s)

Aerial Imaging photography

Industry/Entity Type

Advertising

Contact Information for Business Card

Rowland
0412965203
Website http://www.skywardvistaphoto.com.au/
email address : skywardvistaphoto.com.au

Colors
e8f1ca
cadf82
9bcb3c
33a6d7
85cae6
cee9f5

Requirements
Must have
• High res photo
• Korvane drone in the foreground Either T4200 and korvane Glidewing or both
Nice to have
• high resolution landscape country photo on the front of the card with a Korvane T4200 drone in the foreground.

```html
<!DOCTYPE html>
<html lang="en">
<head>
<meta charset="utf-8">
<title>Skyward Vista – Business Card</title>
<link rel="stylesheet" href="https://fonts.googleapis.com/css2?family=Oswald:wght@600&family=Open+Sans:wght@400;600&display=swap">
<style>
  :root {
    --page-bg: #ecebe8;
    --sky-light: #85cae6;
    --sky-dark: #3d4f5c;
    --band-white: #ffffff;
    --field-light: #9bcb3c;
    --field-mid: #6fb52a;
    --field-dark: #2f8a2a;
    --brand-ink: #2e3338;
    --contact-ink: #ffffff;
  }
  * { box-sizing: border-box; margin: 0; padding: 0; }
  html, body { width: 1200px; height: 900px; overflow: hidden; }
  body { background: var(--page-bg); position: relative; font-family: "Open Sans", Arial, sans-serif; }

  .card {
    position: absolute;
    overflow: hidden;
    background: var(--band-white);
    box-shadow: 0 3px 10px rgba(0,0,0,0.18);
  }
  .card-front { left: 238px; top: 62px; width: 555px; height: 343px; }
  .card-back  { left: 459px; top: 518px; width: 560px; height: 344px; }

  .card-art { position: absolute; inset: 0; width: 100%; height: 100%; display: block; }

  .brand-name {
    position: absolute;
    font-family: "Oswald", "Arial Narrow", sans-serif;
    font-weight: 600;
    color: var(--brand-ink);
    text-transform: uppercase;
    white-space: nowrap;
    line-height: 1;
  }
  .card-front .brand-name {
    left: 0; right: 0; top: 128px;
    text-align: center;
    font-size: 64px;
    letter-spacing: 1px;
  }
  .card-back .brand-name {
    left: 0; right: 0; top: 150px;
    text-align: center;
    font-size: 40px;
    letter-spacing: 1px;
  }

  .holder {
    position: absolute;
    left: 80px; top: 249px;
    color: var(--contact-ink);
    text-align: center;
  }
  .holder-name { font-weight: 600; font-size: 17px; letter-spacing: 0.3px; }
  .holder-role { font-size: 13px; margin-top: 2px; }

  .contact-list {
    position: absolute;
    left: 243px; top: 243px;
    list-style: none;
    color: var(--contact-ink);
    font-size: 13.5px;
  }
  .contact-list li { display: flex; align-items: center; height: 20.5px; }
  .contact-icon { width: 11px; height: 11px; margin-right: 9px; flex: none; }
</style>
</head>
<body>

<section class="card card-front">
  <svg class="card-art" viewBox="0 0 555 343" preserveAspectRatio="none" aria-hidden="true">
    <defs>
      <linearGradient id="frontSky" x1="0" y1="0" x2="0" y2="1">
        <stop offset="0" stop-color="#78b8d9"/>
        <stop offset="1" stop-color="#3d4f5c"/>
      </linearGradient>
      <linearGradient id="frontField" x1="0" y1="0" x2="0" y2="1">
        <stop offset="0" stop-color="#8cc63a"/>
        <stop offset="0.55" stop-color="#5aae2a"/>
        <stop offset="1" stop-color="#2f8a2a"/>
      </linearGradient>
    </defs>
    <rect x="0" y="0" width="555" height="160" fill="url(#frontSky)"/>
    <path d="M0 150 Q277 50 555 150 L555 343 L0 343 Z" fill="var(--band-white)"/>
    <g role="img" aria-label="Green countryside fields seen from above">
      <path d="M0 232 Q277 150 555 232 L555 343 L0 343 Z" fill="url(#frontField)"/>
    </g>
  </svg>

  <h1 class="brand-name">Skyward Vista</h1>

  <div class="holder">
    <p class="holder-name">ELLIS ROWLAND</p>
    <p class="holder-role">General Manager</p>
  </div>

  <ul class="contact-list">
    <li>
      <svg class="contact-icon" viewBox="0 0 12 12" aria-hidden="true"><path d="M2.5 1 L4.5 1 L5.2 3.6 L4 4.6 Q5 6.9 7.4 8 L8.4 6.8 L11 7.5 L11 9.5 Q10.5 11 9 11 Q1 10 1 3 Q1 1.5 2.5 1 Z" fill="#fff"/></svg>
      0412965203
    </li>
    <li>
      <svg class="contact-icon" viewBox="0 0 12 12" aria-hidden="true"><rect x="1" y="2.5" width="10" height="7" fill="#fff"/><path d="M1 2.8 L6 6.5 L11 2.8" fill="none" stroke="#5aae2a" stroke-width="1"/></svg>
      info@skywardvistaphoto.com.au
    </li>
    <li>
      <svg class="contact-icon" viewBox="0 0 12 12" aria-hidden="true"><circle cx="6" cy="6" r="5" fill="#fff"/><path d="M1 6 H11 M6 1 Q3 6 6 11 M6 1 Q9 6 6 11" fill="none" stroke="#5aae2a" stroke-width="0.8"/></svg>
      www.skywardvistaphoto.com.au
    </li>
  </ul>
</section>

<section class="card card-back">
  <svg class="card-art" viewBox="0 0 560 344" preserveAspectRatio="none" aria-hidden="true">
    <defs>
      <linearGradient id="backSky" x1="0" y1="0" x2="0" y2="1">
        <stop offset="0" stop-color="#78b8d9"/>
        <stop offset="1" stop-color="#3d4f5c"/>
      </linearGradient>
      <linearGradient id="backField" x1="0" y1="0" x2="0" y2="1">
        <stop offset="0" stop-color="#7cbd16"/>
        <stop offset="0.5" stop-color="#5aae2a"/>
        <stop offset="1" stop-color="#2f8a2a"/>
      </linearGradient>
    </defs>
    <rect x="0" y="0" width="560" height="112" fill="url(#backSky)"/>
    <rect x="0" y="112" width="560" height="125" fill="var(--band-white)"/>
    <rect x="0" y="237" width="560" height="107" fill="url(#backField)"/>
  </svg>

  <h2 class="brand-name">Skyward Vista</h2>
</section>

</body>
</html>
```